Namibia currently imports 60% of its food. Harvest Crest Oruva is an initiative which will assist Namibia to become self sustainable in terms of food production. We aim to do this through the development of 3 agricultural production zones which will include farming zones, local farmer assistance, processing and distribution of the final products. Please see our project overview attached.

```html
<!DOCTYPE html>
<html lang="en">
<head>
<meta charset="utf-8">
<title>Farmer Empowerment and Education – Harvest Crest Oruva</title>
<link href="https://fonts.googleapis.com/css2?family=Merriweather:wght@400;700&family=Lora:ital,wght@0,400;0,600;1,400&display=swap" rel="stylesheet">
<style>
:root{
  --green:#1f6b3a;
  --green-dark:#174f2b;
  --green-soft:#e8f1ea;
  --gold:#b8895a;
  --text:#222;
  --muted:#555;
  --white:#fff;
  --card-border:#9cc7a6;
}
*{box-sizing:border-box;margin:0;padding:0}
html,body{width:1200px;height:2200px;overflow:hidden;background:var(--white)}
body{font-family:'Lora',Georgia,serif;color:var(--text);position:relative}
.site-header{position:absolute;top:0;left:0;width:1200px;height:112px;background:var(--white);z-index:2}
.brand{position:absolute;left:40px;top:28px;font-family:'Merriweather',Georgia,serif;font-weight:700;font-size:30px;color:var(--green);letter-spacing:1px}
.brand-sub{display:block;font-size:14px;letter-spacing:8px;margin-top:4px}
.contact{position:absolute;top:22px;display:flex;align-items:center;gap:12px}
.contact.call{left:580px}.contact.mail{left:860px}
.contact .dot{width:40px;height:40px;border-radius:50%;background:var(--green);display:flex;align-items:center;justify-content:center}
.contact b{display:block;font-size:15px;color:var(--green)}
.contact span{font-size:15px;color:var(--muted)}
.main-nav{position:absolute;right:40px;top:84px;display:flex;gap:22px;font-size:15px}
.main-nav a{color:var(--text);text-decoration:none}
.main-nav a.active{color:var(--gold)}
.hero{position:absolute;top:112px;left:0;width:1200px;height:548px;background:linear-gradient(100deg,#3f5f34 0%,#6f8f4a 45%,#9fb56a 70%,#c9d6a0 100%)}
.hero h1{position:absolute;left:100px;top:170px;font-family:'Merriweather',Georgia,serif;font-size:52px;line-height:1.3;color:var(--white);font-weight:700}
.play{position:absolute;left:820px;top:340px}
.intro{position:absolute;top:720px;left:0;width:1200px;text-align:center}
.intro h2{font-family:'Merriweather',Georgia,serif;font-size:48px;color:var(--green-dark);font-weight:700}
.quote{margin:52px auto 0;width:740px;font-style:italic;font-size:24px;line-height:1.4;color:var(--gold)}
.lead{margin:40px auto 0;width:1000px;font-size:21px;line-height:1.5;font-weight:600;text-align:left}
.field{position:absolute;top:1340px;left:0;width:1200px;height:390px;background:linear-gradient(180deg,#ffffff 0%,#c9dcb2 25%,#6f9a4e 65%,#4d7a36 100%)}
.skills{position:absolute;top:1100px;left:110px;width:980px;display:grid;grid-template-columns:repeat(4,230px);gap:20px}
.skill{height:215px;background:var(--white);border:2px solid var(--card-border);border-radius:18px;text-align:center;padding-top:34px;font-family:'Merriweather',Georgia,serif;font-size:19px;font-weight:700;color:var(--green-dark);line-height:1.35}
.skill svg{display:block;margin:0 auto 16px}
.site-footer{position:absolute;top:1730px;left:0;width:1200px;height:470px;background:var(--white)}
.footer-brand{position:absolute;left:110px;top:90px;font-family:'Merriweather',Georgia,serif;font-size:64px;font-weight:700;color:var(--green);letter-spacing:4px}
.links{position:absolute;top:0}
.links.quick{left:540px}.links.other{left:920px}
.links h3{font-family:'Merriweather',Georgia,serif;font-size:22px;color:var(--green-dark);margin-bottom:22px}
.links li{list-style:none;font-size:16px;margin-bottom:20px;color:var(--text)}
.copyright{position:absolute;top:2150px;left:0;width:1200px;text-align:center;font-size:14px;color:var(--muted)}
</style>
</head>
<body>
<header class="site-header">
  <div class="brand">HARVEST CREST<span class="brand-sub">ORUVA</span></div>
  <div class="contact call">
    <div class="dot"><svg width="18" height="18" viewBox="0 0 24 24"><path d="M6.6 10.8a15 15 0 006.6 6.6l2.2-2.2a1 1 0 011-.25 11.4 11.4 0 003.6.6 1 1 0 011 1V20a1 1 0 01-1 1A17 17 0 013 4a1 1 0 011-1h3.5a1 1 0 011 1 11.4 11.4 0 00.6 3.6 1 1 0 01-.25 1z" fill="#fff"/></svg></div>
    <div><b>Call Us</b><span>+264 61 555 0142</span></div>
  </div>
  <div class="contact mail">
    <div class="dot"><svg width="18" height="18" viewBox="0 0 24 24"><rect x="3" y="6" width="18" height="12" rx="1" fill="none" stroke="#fff" stroke-width="2"/><path d="M3 7l9 6 9-6" fill="none" stroke="#fff" stroke-width="2"/></svg></div>
    <div><b>Email</b><span>hello@harvestcrest.org</span></div>
  </div>
  <nav class="main-nav">
    <a href="#">Home</a><a href="#">Food Security</a><a href="#" class="active">Farmer Empowerment &amp; Education</a><a href="#">Sustainability</a><a href="#">Contact Us</a>
  </nav>
</header>

<section class="hero" role="img" aria-label="Smiling farmer holding fresh vegetables in a green crop field">
  <h1>Farmer<br>Empowerment<br>and Education</h1>
  <svg class="play" width="72" height="72" viewBox="0 0 72 72"><circle cx="36" cy="36" r="34" fill="#1f3d26"/><path d="M29 23l20 13-20 13z" fill="#fff"/></svg>
</section>

<section class="intro">
  <h2>Farmer Empowerment and Education</h2>
  <p class="quote">“Give a man a fish and feed him for a day, teach a man to fish and feed him for a lifetime”</p>
  <p class="lead">Education is key to empowerment and we embrace that concept. As such, we aim to offer a vocational education scheme for the participants in the Harvest Crest Oruva program. We aim to furnish the participants with the skills to be successful and sustainable farmers in their own rights. Key education outcomes we aim to deliver:</p>
</section>

<div class="field" role="img" aria-label="Rows of green crops stretching across a farm field"></div>

<section class="skills">
  <div class="skill"><svg width="44" height="44" viewBox="0 0 44 44" fill="none" stroke="#b8895a" stroke-width="2"><circle cx="22" cy="12" r="7"/><path d="M8 40c0-9 6-15 14-15s14 6 14 15"/></svg>Farm<br>Management</div>
  <div class="skill"><svg width="44" height="44" viewBox="0 0 44 44" fill="none" stroke="#b8895a" stroke-width="2"><path d="M22 40V14M22 22c-6 0-10-4-10-10 6 0 10 4 10 10zM22 28c6 0 10-4 10-10-6 0-10 4-10 10z"/><path d="M6 40h32"/></svg>Crop<br>Management</div>
  <div class="skill"><svg width="44" height="44" viewBox="0 0 44 44" fill="none" stroke="#b8895a" stroke-width="2"><path d="M22 6c-6 8-9 13-9 17a9 9 0 0018 0c0-4-3-9-9-17z"/><path d="M4 40h36"/></svg>Soil Health<br>and Irrigation</div>
  <div class="skill"><svg width="44" height="44" viewBox="0 0 44 44" fill="none" stroke="#b8895a" stroke-width="2"><circle cx="22" cy="22" r="8"/><circle cx="22" cy="22" r="16" stroke-dasharray="5 4"/></svg>Business<br>Management</div>
  <div class="skill"><svg width="44" height="44" viewBox="0 0 44 44" fill="none" stroke="#b8895a" stroke-width="2"><path d="M6 18h8l16-9v26l-16-9H6z"/><path d="M10 26l3 10h5l-2-10"/></svg>Marketing</div>
  <div class="skill"><svg width="44" height="44" viewBox="0 0 44 44" fill="none" stroke="#b8895a" stroke-width="2"><rect x="5" y="8" width="34" height="22" rx="2"/><path d="M16 38h12M22 30v8"/></svg>Computer<br>Skills</div>
  <div class="skill"><svg width="44" height="44" viewBox="0 0 44 44" fill="none" stroke="#b8895a" stroke-width="2"><rect x="4" y="14" width="22" height="16"/><path d="M26 19h8l6 6v5H26z"/><circle cx="12" cy="33" r="3"/><circle cx="33" cy="33" r="3"/></svg>Logistics<br>Management</div>
  <div class="skill"><svg width="44" height="44" viewBox="0 0 44 44" fill="none" stroke="#b8895a" stroke-width="2"><circle cx="22" cy="22" r="6"/><circle cx="22" cy="22" r="15" stroke-dasharray="6 3" stroke-width="4"/></svg>Vehicle<br>Mechanics</div>
</section>

<footer class="site-footer">
  <div class="footer-brand">HCO</div>
  <div class="links quick">
    <h3>Quick Links</h3>
    <ul><li>Home</li><li>Food Security</li><li>Farmer Empowerment and Education</li><li>Sustainability</li><li>Contact Us</li></ul>
  </div>
  <div class="links other">
    <h3>Other Links</h3>
    <ul><li>Terms and conditions</li><li>Privacy policy</li><li>Career</li><li>Help center</li><li>Support</li></ul>
  </div>
</footer>
<p class="copyright">Copyright © 2019, Harvest Crest Oruva. All rights reserved.</p>
</body>
</html>
```